Classy, Elegant, Simple Business Card Design

Looking to have a classy, simple, and elegant design. Want a top notch designed business card. I really like the look of the new torvane credit card. I also like the design I attached. I am trying to reach 21-29 year old females for booking us for there wedding or event. We offer Disc Jockey Service, Photo Booth Rentals, and Uplighting .

Target Market(s)

21-28 year old females

Contact Information for Business Card

Has to have logo, website, email, and phone number

Font styles to use
Other font styles liked:
• open to font choice, modern, clean
Designer to choose
33a6d7
0791cd
0555a3
ffffff

Requirements
Must have
• Has to have logo, website, email, and phone number
Nice to have
• I really like the design of the new torvane credit card. I also included my logo and some designs I like
Should not have
• clutter or too much info

```html
<!DOCTYPE html>
<html lang="en">
<head>
<meta charset="utf-8">
<title>Tidelight Event Group – Business Card</title>
<link rel="stylesheet" href="https://fonts.googleapis.com/css2?family=Poppins:wght@400;500;600&display=swap">
<style>
  :root {
    --sky: #33a6d7;
    --azure: #0791cd;
    --navy: #0555a3;
    --deep: #164a80;
    --white: #ffffff;
    --ink-grey: #8a8f96;
    --ink-dark: #2f3540;
    --stage: #2b2d31;
  }
  * { box-sizing: border-box; margin: 0; padding: 0; }
  html, body {
    width: 1200px; height: 885px; overflow: hidden;
    background: var(--stage);
    font-family: "Poppins", sans-serif;
  }
  .sheet {
    width: 1200px; height: 885px;
    display: flex; align-items: center; justify-content: center; gap: 40px;
  }
  .card {
    position: relative;
    width: 540px; height: 309px;
    overflow: hidden;
    box-shadow: 0 14px 30px rgba(0,0,0,.45);
  }

  /* Front */
  .card--front {
    background: radial-gradient(ellipse at 60% 45%, var(--sky) 0%, var(--azure) 75%, #0a7fbf 100%);
    display: flex; align-items: center; justify-content: center; gap: 14px;
  }
  .front-mark {
    width: 22px; height: 22px; border-radius: 50%;
    background: var(--navy);
  }
  .front-name {
    color: var(--navy);
    font-weight: 600; font-size: 44px; letter-spacing: 2px;
  }

  /* Back */
  .card--back { background: var(--white); }
  .wave { position: absolute; inset: 0; width: 100%; height: 100%; }
  .brand {
    position: absolute; left: 40px; top: 108px; width: 150px;
    display: flex; align-items: center; gap: 8px;
  }
  .brand-mark { width: 14px; height: 14px; border-radius: 50%; background: var(--azure); flex: none; }
  .brand-name {
    color: var(--navy); font-weight: 600; font-size: 17px; line-height: 1.15;
  }
  .divider {
    position: absolute; left: 210px; top: 70px; width: 1px; height: 110px;
    background: var(--ink-dark);
  }
  .contact { position: absolute; left: 232px; top: 72px; }
  .contact-name { color: var(--azure); font-weight: 600; font-size: 18px; line-height: 1.1; }
  .contact-role { color: var(--ink-grey); font-size: 12px; margin-bottom: 10px; }
  .contact-list { list-style: none; }
  .contact-list li {
    display: flex; align-items: center; gap: 7px;
    color: var(--ink-dark); font-size: 11.5px; line-height: 1.55;
  }
  .contact-list svg { width: 10px; height: 10px; fill: var(--navy); flex: none; }
  .services {
    position: absolute; right: 22px; bottom: 20px;
    color: var(--white); font-size: 12px; font-weight: 500;
    text-align: right; line-height: 1.5;
  }
</style>
</head>
<body>
<main class="sheet">
  <section class="card card--front" aria-label="Card front">
    <span class="front-mark"></span>
    <span class="front-name">TIDELIGHT</span>
  </section>

  <section class="card card--back" aria-label="Card back">
    <svg class="wave" viewBox="0 0 540 309" preserveAspectRatio="none" aria-hidden="true">
      <path d="M0 268 C150 272 250 250 330 205 C400 166 470 148 540 140" fill="none" stroke="var(--sky)" stroke-width="3"/>
      <path d="M0 276 C150 280 250 258 332 213 C402 174 470 156 540 148" fill="none" stroke="var(--azure)" stroke-width="5"/>
      <path d="M0 288 C150 292 252 270 336 224 C406 186 472 166 540 158 L540 309 L0 309 Z" fill="var(--deep)"/>
    </svg>

    <div class="brand">
      <span class="brand-mark"></span>
      <span class="brand-name">Tidelight Event Group</span>
    </div>

    <div class="divider"></div>

    <div class="contact">
      <p class="contact-name">Daniel Harper</p>
      <p class="contact-role">President</p>
      <ul class="contact-list">
        <li><svg viewBox="0 0 10 10"><path d="M2 0.5 L3.8 2.6 L2.9 3.6 C3.5 5 4.9 6.4 6.4 7.1 L7.4 6.2 L9.5 8 L8.3 9.5 C4.5 9.2 0.8 5.5 0.5 1.7 Z"/></svg>555-014-2278</li>
        <li><svg viewBox="0 0 10 10"><path d="M0.5 2 H9.5 V8.5 H0.5 Z M1 2.4 L5 5.5 L9 2.4" stroke="var(--white)" stroke-width="0.8"/></svg>hello@tidelightevents.com</li>
        <li><svg viewBox="0 0 10 10"><circle cx="5" cy="5" r="4.5"/></svg>www.tidelightevents.com</li>
      </ul>
    </div>

    <p class="services">Disc Jockey Service<br>Photo Booth Rentals • Uplighting</p>
  </section>
</main>
</body>
</html>
```